Telecommunications/Power civil contractor needs business card design

Were a new telecommunications/power underground civil contractor that is looking for a new business card design. Our company colours are silver or grey and orange. Feel free to use the white background logo or the black background logo.

Target Market(s)

Local contractors, utility companies, private sector mining/energy companies, developers.

Industry/Entity Type

Telecommunications

Contact Information for Business Card

Each card will need the following info:
Persons name:
Title:
E-mail:
Phone number:
Shop Address:
Mailing Address:

Requirements
Must have
• Each card will need the following info:
• Persons name:
• Title:
• E-mail:
• Phone number:
• Shop Address:
• Mailing Address:

```html
<!DOCTYPE html>
<html lang="en">
<head>
<meta charset="utf-8">
<title>Ridgeline Civil Inc — Business Card</title>
<link rel="stylesheet" href="https://fonts.googleapis.com/css2?family=Open+Sans:wght@400;600;700&display=swap">
<style>
  :root {
    --backdrop: #ececec;
    --card-black: #070707;
    --card-white: #ffffff;
    --brand-orange: #f15a24;
    --brand-grey: #6f6f70;
    --brand-silver: #a9a9ab;
    --text-grey: #4a4a4a;
  }
  * { margin: 0; padding: 0; box-sizing: border-box; }
  html, body {
    width: 1200px; height: 921px; overflow: hidden;
    background: var(--backdrop);
    font-family: "Open Sans", Arial, sans-serif;
  }
  .canvas { position: relative; width: 1200px; height: 921px; }

  .card {
    position: absolute;
    width: 520px; height: 297px;
    overflow: hidden;
    box-shadow: 0 6px 18px rgba(0,0,0,0.18);
  }
  .card--front { left: 130px; top: 130px; background: var(--card-white); }
  .card--back  { left: 550px; top: 494px; background: var(--card-black); }

  .card__art { position: absolute; inset: 0; width: 100%; height: 100%; }

  .brand {
    position: absolute;
    display: flex; flex-direction: column; align-items: center; gap: 14px;
  }
  .card--front .brand { left: 14px; top: 82px; width: 190px; }
  .card--back .brand  { left: 0; right: 0; top: 88px; }
  .brand__dot {
    width: 64px; height: 64px; border-radius: 50%;
    border: 4px solid var(--brand-grey);
  }
  .brand__name {
    color: var(--brand-orange);
    font-weight: 700; font-size: 18px; letter-spacing: 1.2px;
    text-transform: uppercase; white-space: nowrap;
  }
  .card--front .brand__name { font-size: 16px; letter-spacing: 1px; }

  .person {
    position: absolute; right: 26px; top: 26px; text-align: right;
  }
  .person__name {
    color: var(--brand-orange); font-weight: 700; font-size: 18px;
    text-transform: uppercase; letter-spacing: 0.3px;
  }
  .person__title { color: var(--brand-orange); font-size: 13px; }

  .contact {
    position: absolute; right: 22px; bottom: 38px;
    list-style: none; text-align: right;
    color: var(--text-grey); font-size: 12px; line-height: 1.45;
  }
  .contact__item { display: flex; justify-content: flex-end; align-items: center; gap: 7px; margin-top: 6px; }
  .contact__icon { width: 14px; height: 14px; flex: none; }
  .map-texture { position: absolute; inset: 0; }
</style>
</head>
<body>
<main class="canvas">

  <section class="card card--front" aria-label="Business card, front">
    <svg class="card__art" viewBox="0 0 520 297" aria-hidden="true">
      <path d="M0 0 H190 C205 120 215 220 290 297 H0 Z" fill="var(--card-black)"/>
      <path d="M196 0 C211 120 221 220 296 297" fill="none" stroke="var(--brand-orange)" stroke-width="12"/>
      <path d="M214 0 C229 120 239 220 314 297" fill="none" stroke="var(--brand-silver)" stroke-width="7"/>
      <path d="M228 0 C243 120 253 220 328 297" fill="none" stroke="var(--brand-grey)" stroke-width="6"/>
      <path d="M240 0 C255 120 265 220 340 297" fill="none" stroke="var(--brand-orange)" stroke-width="3"/>
    </svg>

    <div class="brand">
      <span class="brand__dot"></span>
      <span class="brand__name">Ridgeline Civil Inc</span>
    </div>

    <div class="person">
      <p class="person__name">Dalton Reyes</p>
      <p class="person__title">Managing Director</p>
    </div>

    <ul class="contact">
      <li class="contact__item">
        <span>240 Quarry Road,<br>Suite 12, Boise, ID 83702</span>
        <svg class="contact__icon" viewBox="0 0 14 14" aria-hidden="true"><circle cx="7" cy="7" r="7" fill="var(--brand-orange)"/><path d="M7 3.2a2.3 2.3 0 0 0-2.3 2.3C4.7 7.3 7 10.6 7 10.6s2.3-3.3 2.3-5.1A2.3 2.3 0 0 0 7 3.2z" fill="#fff"/></svg>
      </li>
      <li class="contact__item">
        <span>555.010.2468</span>
        <svg class="contact__icon" viewBox="0 0 14 14" aria-hidden="true"><circle cx="7" cy="7" r="7" fill="var(--brand-orange)"/><path d="M4.6 3.6l1.4-.2.7 1.8-.9.7a5 5 0 0 0 2.3 2.3l.7-.9 1.8.7-.2 1.4c-3.3.2-6-2.5-5.8-5.8z" fill="#fff"/></svg>
      </li>
      <li class="contact__item">
        <span>office@ridgelinecivil.com</span>
        <svg class="contact__icon" viewBox="0 0 14 14" aria-hidden="true"><circle cx="7" cy="7" r="7" fill="var(--brand-orange)"/><rect x="3.5" y="4.6" width="7" height="4.8" fill="#fff"/><path d="M3.5 4.6L7 7.4l3.5-2.8" fill="none" stroke="var(--brand-orange)" stroke-width="0.8"/></svg>
      </li>
    </ul>
  </section>

  <section class="card card--back" aria-label="Business card, back">
    <div class="map-texture" role="img" aria-label="Faint dotted world map texture" style="background: radial-gradient(ellipse at 55% 45%, #141414 0%, var(--card-black) 70%);"></div>
    <div class="brand">
      <span class="brand__dot"></span>
      <span class="brand__name">Ridgeline Civil Inc</span>
    </div>
  </section>

</main>
</body>
</html>
```